WordPress Site That Reviews Footwear

We need a wordpress web design for an affiliate site called PaceKite. We review and do roundups on footwear products. The final design should be clean and mobile friendly. The site should be built with Gutenberg page builder. We like the design of https://lunavessel.com/.
Updates

Need extra days to review

Target Market(s)

USA

Industry/Entity Type

Footwear

Logo Text

PaceKite

Number of Pages Required

4 page

Font styles to use
Serif
Sans Serif

Requirements
Must have
• Wordpress site
Blog post
Page
Categories
Homepage

```html
<!DOCTYPE html>
<html lang="en">
<head>
<meta charset="utf-8">
<title>5 Easy Shoe Care Tips For Happy Feet – PaceKite</title>
<link rel="stylesheet" href="https://fonts.googleapis.com/css2?family=Playfair+Display:wght@500;700&family=Poppins:wght@400;500;600;700&display=swap">
<style>
:root{
  --ink:#111;
  --text:#3a3a3a;
  --muted:#555;
  --accent:#f5c531;
  --accent-text:#f0b800;
  --band:#f4f4f4;
  --field:#e8e8e8;
  --rule:#dcdcdc;
  --photo-a:#c9c9c9;
  --photo-b:#7d7d7d;
}
*{margin:0;padding:0;box-sizing:border-box}
html,body{width:1200px;height:2382px;overflow:hidden;background:#fff}
body{position:relative;font-family:'Poppins',sans-serif;color:var(--text)}
.abs{position:absolute}

.site-header{left:0;top:0;width:1200px;height:78px}
.main-nav{left:88px;top:34px;display:flex;gap:26px;font-size:14px;color:var(--ink);line-height:18px}
.logo{left:0;width:1200px;top:18px;text-align:center;font-family:'Playfair Display',serif;font-weight:500;font-size:35px;color:var(--ink);line-height:44px}
.aux-nav{left:851px;top:33px;display:flex;gap:26px;font-size:14px;color:var(--ink);line-height:18px}
.header-icon{top:33px}
.cart-count{left:1097px;top:30px;width:13px;height:13px;border-radius:50%;background:var(--accent);font-size:8px;font-weight:600;text-align:center;line-height:13px;color:var(--ink)}

.breadcrumb{left:0;top:78px;width:1200px;height:42px;background:var(--band);padding-left:88px;font-size:15px;line-height:42px;color:var(--ink)}
.breadcrumb .current{font-weight:500}

.hero-photo{left:174px;top:179px;width:845px;height:425px;border-radius:8px;background:linear-gradient(160deg,var(--photo-a) 0%,#a9a9a9 45%,var(--photo-b) 100%)}

.post{left:174px;width:870px}
.post-title{top:630px;font-family:'Playfair Display',serif;font-weight:700;font-size:39px;line-height:50px;color:var(--ink);white-space:nowrap}
.post-date{top:680px;font-size:17.5px;line-height:24px;color:var(--muted)}
.body-text{font-size:15.6px;line-height:26.7px;color:var(--text);white-space:nowrap}
.p1{top:714px}
.sub-heading{font-size:17.5px;font-weight:700;color:var(--ink);line-height:24px}
.h-shop{top:887px;left:172px}
.collection{top:917px;left:172px;list-style:none;font-size:15.6px;line-height:28.7px;white-space:nowrap}
.p2{top:1018px}
.h-testi{top:1150px;left:172px}
.quote{top:1190px;font-size:15.6px;line-height:26.7px;white-space:nowrap}
.quote sup{font-size:18px;line-height:0}
.attribution{top:1280px;font-size:17.5px;font-weight:600;color:var(--accent-text);line-height:24px}
.attribution span{margin-right:24px}
.share{left:0;width:1200px;top:1357px;text-align:center;font-size:18.5px;font-weight:500;color:var(--ink);line-height:26px}
.share a{color:inherit;text-decoration:underline;text-underline-offset:6px;text-decoration-thickness:1px}

.comment-title{left:172px;top:1455px;font-family:'Playfair Display',serif;font-weight:700;font-size:39px;line-height:50px;color:var(--ink)}
.comment-rule{left:172px;top:1511px;width:853px;height:1px;background:var(--rule)}
.field{background:var(--field);font-size:17.5px;font-weight:500;color:var(--ink);padding:0 21px}
.f-name{left:273px;top:1576px;width:323px;height:49px;line-height:49px}
.f-email{left:603px;top:1576px;width:323px;height:49px;line-height:49px}
.f-comment{left:273px;top:1634px;width:653px;height:192px;padding-top:14px;line-height:24px}
.submit{left:479px;top:1840px;width:241px;height:51px;border-radius:8px;background:var(--accent);text-align:center;line-height:51px;font-size:18.5px;font-weight:700;color:var(--ink);letter-spacing:.3px}

.site-footer{left:0;top:1983px;width:1200px;height:399px;background:var(--band)}
.f-col{top:2082px}
.f-col h4{font-family:'Playfair Display',serif;font-weight:700;font-size:18.5px;text-transform:uppercase;color:var(--ink);line-height:24px;margin-bottom:4px;letter-spacing:.2px}
.f-col ul{list-style:none;font-size:13px;line-height:22.2px;color:var(--muted);padding-left:1px}
.newsletter{left:824px;top:2106px;width:286px;height:45px;border-bottom:3px solid var(--accent);font-size:22px;font-weight:600;color:#bdbdbd;padding-left:4px;line-height:34px}
.newsletter svg{position:absolute;right:8px;top:8px}
.to-top{left:1139px;top:2304px;width:32px;height:32px;border-radius:50%;background:var(--accent)}
.footer-rule{left:88px;top:2324px;width:1023px;height:1px;background:var(--rule)}
.copyright{left:88px;top:2344px;font-size:14px;line-height:20px;color:var(--ink)}
.pay{top:2343px;height:24px;border-radius:5px}
</style>
</head>
<body>

<header class="site-header abs">
  <nav class="main-nav abs"><span>WOMENS</span><span>MENS</span><span>KIDS</span><span>SALE</span></nav>
  <div class="logo abs">PaceKite</div>
  <nav class="aux-nav abs"><span>ABOUT</span><span>CONTACT</span></nav>
  <svg class="header-icon abs" style="left:1023px" width="18" height="18" viewBox="0 0 18 18" fill="none" stroke="#111" stroke-width="2"><circle cx="7.5" cy="7.5" r="6"/><path d="M12 12l5 5"/></svg>
  <svg class="header-icon abs" style="left:1054px" width="17" height="18" viewBox="0 0 17 18" fill="none" stroke="#111" stroke-width="1.6"><circle cx="8.5" cy="5.5" r="4.5"/><path d="M1 17.5c0-4.5 3.3-7 7.5-7s7.5 2.5 7.5 7"/></svg>
  <svg class="header-icon abs" style="left:1084px" width="17" height="18" viewBox="0 0 17 18" fill="none" stroke="#111" stroke-width="1.6"><path d="M2 6h13l-1 11H3z"/><path d="M5.5 6V4a3 3 0 016 0v2"/></svg>
  <div class="cart-count abs">0</div>
</header>

<div class="breadcrumb abs">Home &gt; Blog Post &gt; <span class="current">5 Easy Shoe Care Tips For Happy Feet</span></div>

<div class="hero-photo abs" role="img" aria-label="Black and white photo of white leather sneakers and dark trousers on a speckled stone floor beside a wall"></div>

<article>
  <h1 class="post post-title abs">5 Easy Shoe Care Tips For Happy Feet</h1>
  <p class="post post-date abs">Date: Aug-10-2020</p>
  <p class="post body-text p1 abs">Lorem Ipsum is simply dummy text of the printing and typesetting industry. Lorem Ipsum has been the indus-<br>try's standard dummy text ever since the 1500s, when an unknown printer took a galley of type and scrambled it<br>to make a type specimen book. It has survived not only five centuries, but also the leap into electronic typeset-<br>ting, remaining essentially unchanged. It was popularised in the 1960s with the release of Typeleaf sheets con-<br>taining Lorem Ipsum passages, and more recently with desktop publishing software like Folio Layout<br>including versions of Lorem Ipsum.</p>
  <h3 class="sub-heading h-shop abs">Shop Our Collection:</h3>
  <ul class="collection abs">
    <li>Men’s - Strider Glide 9 Charcoal/Black available in medium width and wide width</li>
    <li>Women’s - Strider Glide 9 Coral available in medium width</li>
    <li>Women’s - Strider Glide 9 Blush/Dusk available in medium width and wide width</li>
  </ul>
  <p class="post body-text p2 abs">Lorem Ipsum is simply dummy text of the printing and typesetting industry. Lorem Ipsum has been the indus-<br>try's standard dummy text ever since the 1500s, when an unknown printer took a galley of type and scrambled it<br>to make a type specimen book. It has survived not only five centuries, but also the leap into electronic typeset-<br>ting, remaining essentially unchanged. It was popularised in the 1960s .</p>
  <h3 class="sub-heading h-testi abs">Testimonials</h3>
  <blockquote class="post quote abs"><sup>”</sup>Lorem Ipsum is simply dummy text of the printing and typesetting industry. Lorem Ipsum has been the indus-<br>try's standard dummy text ever since the 1500s, when an unknown printer took a galley of type and scram-<br>bled it to make a type specimen book. It has survived not only five centuries<sup>”</sup></blockquote>
  <p class="post attribution abs"><span>-</span>Mara Quillen, Strider Athlete</p>
  <p class="share abs"><a href="#">Share this blog to your friends</a></p>
</article>

<section>
  <h2 class="comment-title abs">Post Comment</h2>
  <div class="comment-rule abs"></div>
  <div class="field f-name abs">Name</div>
  <div class="field f-email abs">Email</div>
  <div class="field f-comment abs">Comment</div>
  <div class="submit abs">SUBMIT COMMENT</div>
</section>

<footer>
  <div class="site-footer abs"></div>
  <div class="f-col abs" style="left:88px"><h4>Company Info</h4><ul><li>About</li><li>Corporate video</li><li>Blog</li><li>Contact Us</li></ul></div>
  <div class="f-col abs" style="left:338px"><h4>What's in store</h4><ul><li>New Arrivals</li><li>Men</li><li>Women</li><li>Kids</li><li>Accessories</li><li>Brands</li></ul></div>
  <div class="f-col abs" style="left:596px"><h4>Help &amp; Support</h4><ul><li>Exchange &amp; Returns</li><li>Privacy Policy</li><li>FAQ</li></ul></div>
  <div class="newsletter abs">Enter your email
    <svg width="20" height="18" viewBox="0 0 20 18"><path d="M1 8L19 1l-5 16-4-6z" fill="#111"/></svg>
  </div>
  <div class="to-top abs"><svg width="32" height="32" viewBox="0 0 32 32" fill="none" stroke="#111" stroke-width="1.6"><path d="M13 18l3-3 3 3"/></svg></div>
  <div class="footer-rule abs"></div>
  <p class="copyright abs">©Copyright 2021 | All Rights Reserved</p>
  <div class="pay abs" style="left:980px;width:22px;background:#cfd6e6"></div>
  <div class="pay abs" style="left:1018px;width:44px;background:#2b3bb5"></div>
  <div class="pay abs" style="left:1077px;width:26px;background:#e3e3e3;border-radius:50%"></div>
</footer>

</body>
</html>
```